Business Card Design

Company is a Commercial Building Company specialising in New Construction and existing refurbishments

Industry/Entity Type

Business

Contact Information for Business Card

Liam Porter
Construction Manager
E Liam@marshbuilding.com.au
M 0400 213 594
Mail 14 Tarrant Rise Tarrant Bay WA 6180

```html
<!DOCTYPE html>
<html lang="en">
<head>
<meta charset="utf-8">
<title>Marsh Building &amp; Construction – Business Card</title>
<link rel="stylesheet" href="https://fonts.googleapis.com/css2?family=Saira:wght@500;600&family=Questrial&display=swap">
<style>
  :root {
    --bg: #e9e6e1;
    --gold-light: #fcd277;
    --gold: #f3b431;
    --gold-deep: #e38e1c;
    --ink: #0d0d0d;
    --card-black: #050505;
    --white: #f4f4f4;
    --accent-orange: #f2a623;
    --teal: #12b7c9;
  }
  * { box-sizing: border-box; margin: 0; padding: 0; }
  html, body { width: 1200px; height: 858px; overflow: hidden; }
  body {
    background: var(--bg);
    display: flex;
    align-items: center;
    justify-content: center;
    gap: 70px;
    font-family: "Questrial", "Century Gothic", sans-serif;
  }

  /* Front: landscape, gold */
  .card-front {
    width: 580px;
    height: 332px;
    border-radius: 4px;
    background: radial-gradient(ellipse at 45% 50%, var(--gold-light) 0%, var(--gold) 55%, var(--gold-deep) 100%);
    box-shadow: 0 12px 30px rgba(0,0,0,.25);
    display: flex;
    flex-direction: column;
    justify-content: center;
    padding-left: 62px;
  }
  .front-wordmark {
    font-family: "Saira", "Eurostile", sans-serif;
    font-weight: 500;
    color: var(--ink);
    text-transform: uppercase;
    line-height: 1.02;
    font-size: 52px;
    letter-spacing: 0.5px;
  }

  /* Back: portrait, black */
  .card-back {
    width: 320px;
    height: 560px;
    border-radius: 4px;
    background: var(--card-black);
    box-shadow: 0 12px 30px rgba(0,0,0,.3);
    position: relative;
    overflow: hidden;
    color: var(--white);
  }
  .brand {
    position: absolute;
    top: 92px;
    left: 36px;
    right: 30px;
  }
  .brand-square {
    width: 34px;
    height: 34px;
    background: var(--accent-orange);
    margin-bottom: 18px;
  }
  .brand-name {
    font-family: "Saira", "Eurostile", sans-serif;
    font-weight: 500;
    font-size: 24px;
    line-height: 1.05;
    text-transform: uppercase;
    color: var(--white);
  }
  .person {
    position: absolute;
    top: 262px;
    left: 96px;
  }
  .person-name {
    font-family: "Saira", "Eurostile", sans-serif;
    font-weight: 500;
    font-size: 20px;
    letter-spacing: .5px;
    text-transform: uppercase;
    color: var(--accent-orange);
    line-height: 1;
  }
  .person-role { font-size: 12px; margin-top: 3px; }
  .contact {
    position: absolute;
    left: 70px;
    right: 24px;
    font-size: 15px;
    line-height: 1.3;
  }
  .contact-direct { top: 352px; }
  .contact-address { top: 432px; }
  .band-rule {
    position: absolute;
    left: 0; right: 0;
    bottom: 38px;
    height: 2px;
    background: var(--accent-orange);
  }
  .band {
    position: absolute;
    left: 0; right: 0; bottom: 0;
    height: 38px;
    background: var(--teal);
  }
</style>
</head>
<body>
  <section class="card-front" aria-label="Business card front">
    <p class="front-wordmark">Marsh Building<br>&amp; Construction</p>
  </section>

  <section class="card-back" aria-label="Business card back">
    <div class="brand">
      <div class="brand-square"></div>
      <p class="brand-name">Marsh Building<br>&amp; Construction</p>
    </div>
    <div class="person">
      <p class="person-name">Liam Porter</p>
      <p class="person-role">Construction Manager</p>
    </div>
    <div class="contact contact-direct">
      <p>0400 213 594</p>
      <p>Liam@marshbuilding.com.au</p>
    </div>
    <div class="contact contact-address">
      <p>14 Tarrant Rise</p>
      <p>Tarrant Bay WA 6180</p>
    </div>
    <div class="band-rule"></div>
    <div class="band"></div>
  </section>
</body>
</html>
```